Veterinary Pylon

My veterinary clinic is not clearly visible from the street and I want to place a Pylon next to my driveway. I want a modern, elegant straight Design, the Photo shows the sheduled place. One can see the clinic on our Homepage: www.tailbright-vethaus.at
The last pictures are examples for pylones I like

Target Market(s)

the passing cars often miss my entry...I want to show where to turn left

Colors
3276b5
33a6d7
00a990

Requirements
Must have
• High value, simple elegance, size: 250cm (high) x 100cm (width)
Nice to have
• Our Logo, arrow(?)

A special Text is not necessary but this will be an option:

Biegen sie hier ab und wir biegen es wieder hin!
Should not have
• Too much Color, the colors I have chosen are the possible colors but it‘s not necessary to use them.

```html
<!DOCTYPE html>
<html lang="de">
<head>
<meta charset="utf-8">
<title>Tailbright Vethaus – Pylon</title>
<link rel="stylesheet" href="https://fonts.googleapis.com/css2?family=Archivo+Black&display=swap">
<style>
  :root {
    --navy: #104a92;
    --sky: #2ebbdf;
    --paper: #ffffff;
  }
  * { margin: 0; padding: 0; box-sizing: border-box; }
  html, body {
    width: 1200px;
    height: 3000px;
    overflow: hidden;
    background: var(--paper);
  }
  .pylon {
    position: relative;
    width: 1200px;
    height: 3000px;
    background: var(--paper);
    overflow: hidden;
  }
  .brand-mark {
    position: absolute;
    top: 80px;
    left: 395px;
    width: 410px;
    height: 410px;
  }
  .brand-name {
    position: absolute;
    left: 0;
    width: 1200px;
    text-align: center;
    font-family: "Archivo Black", sans-serif;
    font-weight: 400;
    line-height: 1;
    white-space: nowrap;
  }
  .brand-name .line-main {
    display: block;
    font-size: 112px;
    letter-spacing: 0;
  }
  .brand-name .line-sub {
    display: block;
    margin-top: 44px;
    font-size: 70px;
    letter-spacing: 26px;
    padding-left: 26px;
  }
  .brand-name--top {
    top: 640px;
    color: var(--navy);
  }
  .brand-name--base {
    top: 2520px;
    color: var(--paper);
  }
  .brand-name--base .line-main { font-size: 132px; }
  .brand-name--base .line-sub { font-size: 82px; letter-spacing: 30px; padding-left: 30px; margin-top: 54px; }
  .turn-arrow {
    position: absolute;
    top: 1095px;
    left: 430px;
    width: 370px;
    height: 290px;
  }
  .base-waves {
    position: absolute;
    left: 0;
    top: 1480px;
    width: 1200px;
    height: 1520px;
  }
</style>
</head>
<body>
  <main class="pylon">
    <svg class="brand-mark" viewBox="0 0 410 410" aria-hidden="true">
      <circle cx="205" cy="205" r="190" fill="none" stroke="var(--sky)" stroke-width="18"/>
    </svg>

    <h1 class="brand-name brand-name--top">
      <span class="line-main">TAILBRIGHT</span>
      <span class="line-sub">VETHAUS</span>
    </h1>

    <svg class="turn-arrow" viewBox="0 0 370 290" aria-label="Pfeil nach links: hier abbiegen" role="img">
      <defs>
        <linearGradient id="arrowFade" x1="0" y1="0" x2="1" y2="0">
          <stop offset="0" stop-color="#1b5fa5"/>
          <stop offset="1" stop-color="#2ebbdf"/>
        </linearGradient>
      </defs>
      <path d="M145 6 L145 50 L78 117 L362 117 L362 146 L78 146 L145 213 L145 281 L7 143.5 Z"
            fill="url(#arrowFade)"/>
    </svg>

    <svg class="base-waves" viewBox="0 1480 1200 1520" preserveAspectRatio="none" aria-hidden="true">
      <path d="M0 1515 Q 260 1505 540 1640 L 0 2000 Z" fill="var(--sky)"/>
      <path d="M0 1830 Q 360 1578 790 1578 Q 1010 1580 1200 1640 L 1200 3000 L 0 3000 Z" fill="var(--navy)"/>
    </svg>

    <p class="brand-name brand-name--base">
      <span class="line-main">TAILBRIGHT</span>
      <span class="line-sub">VETHAUS</span>
    </p>
  </main>
</body>
</html>
```